Lotstallmart.com Webpage Design

Design Brief for lotstallmart.com (Copy of Brief also in attached Word file)

Name of Website- lotstallmart.com (existing logo and look & feel of website to be changed)

Logo - Finalised. The logo files are attached with the brief as “logo.jpeg”. The “Blue- Grey” version of the logo is for use on lighter backgrounds and the “Orange-White” version of the logo is for use on darker backgrounds. (A full Black version of the logo is also attached). Both versions may be used in different parts of the website. All attached files are in .png format.
Status - The website in functional and is undergoing user trials. However, we want to improve the look & feel of the website so at it seems
a. cotemporary,
b. Easy to Navigate
c. professional and
d. Vibrant.

Please visit ‘lotstallmart.com’ to check out the website and its functionalities – please use it only as a reference for the features & functions to be provided, however the designer should use a ‘Free Hand’ in designing the composition of various parts of the webpage without getting too influenced by the existing design

Objective of the Website ‘lotstallmart.com –
a. It is a portal focussed on listing of ‘Retail’ specific real-estate properties by developers, owners and realty brokers. The properties shall listed under the following four categories-
i. Retail Malls
ii. Shopping Complexes
iii. High-street shops
iv. Retail Warehouses
*refer lotstallmart.com for better clarity

b. The abovementioned properties shall be listed either for ‘Sale’ or ‘rent\lease’ or both

c. Users shall visit the site in case they wish to acquire a retail \ shop space either on ‘sale’ or ‘rent’. These Users would be able to specify the ‘Search Criteria’ through the tool-bars provided on the website – the ‘Search Criteria’ shall comprise of ‘Type of space category’, ‘City’, ‘Locality’, transaction type ie ‘Rent \ Sale’ and ‘Area Range’

d. The main revenue model for the website shall be listing fee ( or advertising charges ) payable by those listing their properties on the website.

Three Main Pages of Website (lotstallmart.com) that need to be designed -
a. Main Home Page (visit the web link - http://lotstallmart.com/ ) - The main home page has the “Search Toolbar” for specifying of Search Criteria by the User. It shall also have the following features & functions-
i. Main Advertising Banner
ii. Featured Projects
iii. New Launches
iv. Toolbar with buttons – ‘Advertise with Us’, ‘Listings Alert’, ‘Mart Wizards’, ‘Advertiser Login’

b. Property Listings Page (visit the web link - http://lotstallmart.com/gurgaon-in-india ) - The List of property options that match the Criteria specified by the ‘User’ get displayed on this page.

c. Property Detail Page - When the ‘User’ clicks on the “More….” Button on the ‘Property Listings Page’ (given in point b. above) the web page with the details of the property opens. (For Example – visit the web link - http://lotstallmart.com/vorne-Shopping-Complex-vorne-quadrion-gurgaon-636 )

Note:- Please refer to attached ‘Shopping’ related images the designer may use them on the website to provide a look & feel of retail if required – either separately or rotate in a single window

Target Market(s)

Retailers & Investors looking for retail space, Real Estate Brokers, Developers

Industry/Entity Type

Advertising

Number of Pages Required

3 page

Requirements
Must have
• Refer to existing site lotstallmart.com -- all the existing functionalities are a must have.
Nice to have
• The Designer may use the retail related images on the website if required for making it more vibrant. Refer attached images Shopping(1-6).jpg

```html
<!DOCTYPE html>
<html lang="en">
<head>
<meta charset="utf-8">
<title>Lotstallmart.com – India's Leading Portal for Retail Space</title>
<link rel="stylesheet" href="https://fonts.googleapis.com/css2?family=Ubuntu:wght@400;500;700&family=Arimo:wght@400;700&display=swap">
<style>
:root{
  --orange:#f0a23a;
  --orange-deep:#e8922a;
  --charcoal:#3f3f3f;
  --bar:#2d2d2d;
  --header:#4b4b4b;
  --ink:#2b2b2b;
  --muted:#8a8a8a;
  --line:#dcdcdc;
  --soft:#f1f1f1;
  --white:#fff;
}
*{box-sizing:border-box;margin:0;padding:0}
html,body{width:722px;height:1200px;overflow:hidden}
body{position:relative;font-family:Arimo,Arial,sans-serif;background:var(--white);color:var(--ink)}
.abs{position:absolute}

/* header */
.site-header{position:absolute;left:0;top:0;width:722px;height:54px;background:var(--header)}
.city-strip{position:absolute;left:232px;top:0;width:490px;height:18px;background:var(--orange);
  clip-path:polygon(12px 0,100% 0,100% 100%,0 100%);
  color:var(--white);font-size:7.3px;line-height:18px;padding-left:24px;white-space:nowrap}
.brand{position:absolute;left:62px;top:8px;display:flex;align-items:center;gap:6px}
.brand-dot{width:14px;height:14px;border-radius:50%;background:var(--orange)}
.brand-name{font-family:Ubuntu,sans-serif;font-weight:500;font-size:17px;color:var(--white)}
.brand-tag{position:absolute;left:82px;top:30px;font-family:Ubuntu,sans-serif;font-size:4.6px;color:var(--orange);letter-spacing:.3px;white-space:nowrap}
.main-nav{position:absolute;top:30px;left:376px;display:flex;gap:25px;font-family:Ubuntu,sans-serif;font-weight:500;font-size:9.6px;color:var(--white)}

/* hero */
.hero{position:absolute;left:0;top:54px;width:722px;height:318px;
  background:linear-gradient(90deg,#f3b766 0%,#eeb25c 38%,#e9c9a0 52%,#d8d0c6 70%,#c9c4bd 100%)}
.search-panel{position:absolute;left:0;top:54px;width:280px;height:318px}
.panel-title{position:absolute;left:62px;top:21px;font-size:7.6px;font-weight:700;color:#222}
.close-btn{position:absolute;left:256px;top:60px}
.format-box{position:absolute;left:63px;top:96px;width:176px;height:41px;background:var(--bar);border-radius:3px;color:var(--white);font-size:7px}
.format-box span{position:absolute;display:flex;align-items:center;gap:5px}
.format-box i{display:block;width:7px;height:7px;background:var(--white)}
.field-label{position:absolute;left:66px;font-size:7.4px;color:#222}
.field{position:absolute;left:64px;width:174px;height:21px;background:var(--white);border-radius:2px;font-size:7px;color:#555;line-height:21px;padding-left:6px}
.search-btn{position:absolute;left:64px;top:337px;width:65px;height:20px;background:var(--bar);border-radius:3px;color:var(--white);font-size:10.5px;text-align:center;line-height:20px}

/* categories */
.category-bar{position:absolute;left:0;top:372px;width:722px;height:63px;background:var(--bar)}
.category{position:absolute;top:0;height:63px;display:flex;align-items:center;gap:9px}
.category + .category{}
.divider{position:absolute;top:0;width:1px;height:63px;background:#444}
.cat-title{font-family:Ubuntu,sans-serif;font-weight:500;font-size:8.8px;color:var(--orange)}
.cat-sub{font-family:Ubuntu,sans-serif;font-weight:500;font-size:7.8px;color:var(--white);margin-top:3px}

/* listings */
.section-title{position:absolute;left:0;width:722px;text-align:center;font-family:Ubuntu,sans-serif;font-size:17.5px;color:#333}
.section-title em{font-style:normal;font-size:11px;color:var(--orange)}
.rule{position:absolute;height:1px;background:#bbb}
.launches-bg{position:absolute;left:0;top:710px;width:722px;height:262px;background:var(--soft)}
.grid{position:absolute;left:61px;display:grid;grid-template-columns:292px 292px;column-gap:16px;row-gap:17px}
.card{position:relative;height:87px;background:var(--white);border:1px solid var(--line)}
.card-img{position:absolute;left:5px;top:5px;width:114px;height:77px;overflow:hidden}
.ribbon{position:absolute;left:-20px;top:14px;width:70px;height:10px;transform:rotate(-45deg);background:var(--orange);color:var(--white);font-size:5.2px;text-align:center;line-height:10px;letter-spacing:.3px}
.ribbon.dark{background:#333}
.card-city{position:absolute;left:131px;top:5px;font-family:Ubuntu,sans-serif;font-size:13px;color:var(--orange)}
.card-name{position:absolute;left:131px;top:24px;font-family:Ubuntu,sans-serif;font-weight:700;font-size:7.3px;color:#222}
.card-desc{position:absolute;left:131px;top:35px;width:157px;font-size:5.9px;line-height:10.5px;color:var(--muted)}
.card-btn{position:absolute;left:129px;top:61px;width:69px;height:15px;background:var(--bar);color:var(--white);font-family:Ubuntu,sans-serif;font-weight:700;font-size:7px;text-align:center;line-height:15px}
.img-a{background:linear-gradient(160deg,#cfd5da 0%,#8a6a52 45%,#3a2e28 100%)}
.img-b{background:linear-gradient(180deg,#6b4b45 0%,#8b4f3c 45%,#2f5f78 80%,#1d3e55 100%)}
.img-c{background:linear-gradient(180deg,#b8c6d6 0%,#e3dccf 50%,#7b7463 100%)}
.img-d{background:linear-gradient(180deg,#6f8fb7 0%,#c89a5e 60%,#7a4a22 100%)}

/* footer */
.site-footer{position:absolute;left:0;top:972px;width:722px;height:173px;background:var(--charcoal);color:var(--white)}
.foot-h{position:absolute;top:16px;font-family:Ubuntu,sans-serif;font-weight:500;font-size:13px;color:var(--white)}
.foot-vr{position:absolute;top:11px;width:1px;height:133px;background:#777}
.foot-text{position:absolute;font-size:7.2px;line-height:12px;color:var(--white)}
.foot-input{position:absolute;background:var(--white);color:#999;font-size:7px;padding:5px 5px}
.foot-btn{position:absolute;background:var(--orange);border-radius:3px;color:var(--white);font-family:Ubuntu,sans-serif;font-weight:700;text-align:center}
.bottom-band{position:absolute;left:0;top:1145px;width:722px;height:55px;background:var(--orange)}
.copyright{position:absolute;left:57px;top:17px;font-size:7.6px;line-height:16px;color:#2a2a2a}
.band-brand{position:absolute;left:508px;top:13px;display:flex;align-items:center;gap:6px}
.band-brand .brand-dot{background:#2a2a2a}
.band-brand .brand-name{font-size:16px}
.band-tag{position:absolute;left:549px;top:36px;font-family:Ubuntu,sans-serif;font-weight:700;font-size:4.6px;color:#2a2a2a;white-space:nowrap}
</style>
</head>
<body>

<header class="site-header">
  <div class="city-strip">Bangalore | Chennai | Greater Noida | Gurgaon | Hyderabad | Jaipur | Khanna | Kolkatta | Mumbai | Noida | Pune | Surat</div>
  <div class="brand"><span class="brand-dot"></span><span class="brand-name">lotstallmart</span></div>
  <div class="brand-tag">INDIA'S LEADING PORTAL FOR RETAIL SPACE</div>
  <nav class="main-nav"><span>Home</span><span>Advertise with us</span><span>Mart Wizards</span><span>Listing Alert</span></nav>
</header>

<div class="hero" role="img" aria-label="Banner photo of a smiling couple with shopping bags looking at a tablet in a warm-lit mall"></div>

<form class="search-panel">
  <div class="panel-title">Select Retail Format: Meaning of Retail Format</div>
  <svg class="close-btn" width="22" height="22" viewBox="0 0 22 22"><circle cx="11" cy="11" r="9.5" fill="none" stroke="#222" stroke-width="1.2"/><path d="M6.5 6.5l9 9M15.5 6.5l-9 9" stroke="#222" stroke-width="1.2"/></svg>
</form>
<div class="format-box">
  <span style="left:9px;top:9px"><i></i>Retail Malls</span>
  <span style="left:81px;top:9px"><i></i>Shopping Complex</span>
  <span style="left:9px;top:26px"><i></i>High Street Sh</span>
  <span style="left:81px;top:26px"><i></i>Retail Warehouses</span>
</div>
<div class="field-label" style="top:155px">Sale Or Rent Or Both:</div>
<div class="field" style="top:169px">Both</div>
<div class="field-label" style="top:201px">Select City-</div>
<div class="field" style="top:213px">-Select-</div>
<div class="field-label" style="top:246px">Select Locality/Micro-Market.</div>
<div class="field" style="top:258px">-Select-</div>
<div class="field-label" style="top:290px">Enter Keywords:</div>
<div class="field" style="top:303px">Name of Project,Developer etc</div>
<div class="search-btn">SEARCH</div>

<section class="category-bar">
  <div class="category" style="left:65px">
    <svg width="24" height="24" viewBox="0 0 24 24"><circle cx="12" cy="12" r="10" fill="none" stroke="#fff" stroke-width="2"/><text x="12" y="16" font-size="10" fill="#fff" text-anchor="middle" font-family="Arial">€$</text></svg>
    <div><div class="cat-title">Retail Malls</div><div class="cat-sub">Centrally Air-Conditioned</div></div>
  </div>
  <div class="divider" style="left:208px"></div>
  <div class="category" style="left:217px">
    <svg width="22" height="22" viewBox="0 0 22 22"><rect x="2" y="12" width="3" height="9" fill="#fff"/><rect x="7" y="9" width="3" height="12" fill="#fff"/><rect x="12" y="6" width="3" height="15" fill="#fff"/><rect x="17" y="3" width="3" height="18" fill="#fff"/></svg>
    <div><div class="cat-title">Shopping Complex</div><div class="cat-sub">Non Air-Conditioned Building</div></div>
  </div>
  <div class="divider" style="left:371px"></div>
  <div class="category" style="left:382px">
    <svg width="26" height="22" viewBox="0 0 26 22"><path d="M13 1L2 8h22z" fill="#fff"/><rect x="3" y="9" width="20" height="12" fill="#fff"/><rect x="6" y="12" width="3" height="3" fill="#2d2d2d"/><rect x="17" y="12" width="3" height="3" fill="#2d2d2d"/><rect x="11" y="13" width="4" height="8" fill="#2d2d2d"/></svg>
    <div><div class="cat-title">High Street Shops</div><div class="cat-sub">Road Facing Retail</div></div>
  </div>
  <div class="divider" style="left:509px"></div>
  <div class="category" style="left:524px">
    <svg width="28" height="26" viewBox="0 0 28 26"><rect x="3" y="6" width="20" height="12" rx="2" fill="none" stroke="#fff" stroke-width="2" transform="rotate(15 13 12)"/><rect x="6" y="10" width="20" height="12" rx="2" fill="#fff" transform="rotate(15 16 16)"/></svg>
    <div><div class="cat-title">Retail Warehouses</div><div class="cat-sub">Back-end Ratail Storage</div></div>
  </div>
</section>

<!-- Featured Retail Projects -->
<div class="rule" style="left:65px;top:461px;width:157px"></div>
<div class="rule" style="left:500px;top:461px;width:157px"></div>
<h2 class="section-title" style="top:450px;font-weight:400">Featured Retail Projects <em>Across India</em></h2>

<div class="grid" style="top:487px">
  <article class="card"><div class="card-img img-a" role="img" aria-label="Photo of a mid-rise brick apartment block"><span class="ribbon">FEATURED</span></div><div class="card-city">Gurgaon</div><div class="card-name">Veltra Cosmoline</div><p class="card-desc">The images for this demonstration property were kindly loaned to us by the Corvane Estate Group and a...</p><a class="card-btn">View Property</a></article>
  <article class="card"><div class="card-img img-b" role="img" aria-label="Photo of a modern villa with a lit pool at dusk"><span class="ribbon">FEATURED</span></div><div class="card-city">Gurgaon</div><div class="card-name">Veltra Cosmoline</div><p class="card-desc">The images for this demonstration property were kindly loaned to us by the Corvane Estate Group and a...</p><a class="card-btn">View Property</a></article>
  <article class="card"><div class="card-img img-c" role="img" aria-label="Photo of white suburban townhouses"><span class="ribbon">FEATURED</span></div><div class="card-city">Gurgaon</div><div class="card-name">Veltra Cosmoline</div><p class="card-desc">The images for this demonstration property were kindly loaned to us by the Corvane Estate Group and a...</p><a class="card-btn">View Property</a></article>
  <article class="card"><div class="card-img img-d" role="img" aria-label="Photo of a tall hotel tower lit at evening"><span class="ribbon">FEATURED</span></div><div class="card-city">Gurgaon</div><div class="card-name">Veltra Cosmoline</div><p class="card-desc">The images for this demonstration property were kindly loaned to us by the Corvane Estate Group and a...</p><a class="card-btn">View Property</a></article>
</div>

<!-- Featured New Launches -->
<div class="launches-bg"></div>
<div class="rule" style="left:67px;top:728px;width:155px"></div>
<div class="rule" style="left:500px;top:728px;width:157px"></div>
<h2 class="section-title" style="top:716px;font-weight:400">Featured New Launches <em>Across India</em></h2>

<div class="grid" style="top:759px">
  <article class="card"><div class="card-img img-a" role="img" aria-label="Photo of a mid-rise brick apartment block"><span class="ribbon dark">FEATURED</span></div><div class="card-city">Gurgaon</div><div class="card-name">Veltra Cosmoline</div><p class="card-desc">The images for this demonstration property were kindly loaned to us by the Corvane Estate Group and a...</p><a class="card-btn">View Property</a></article>
  <article class="card"><div class="card-img img-b" role="img" aria-label="Photo of a modern villa with a lit pool at dusk"><span class="ribbon dark">FEATURED</span></div><div class="card-city">Gurgaon</div><div class="card-name">Veltra Cosmoline</div><p class="card-desc">The images for this demonstration property were kindly loaned to us by the Corvane Estate Group and a...</p><a class="card-btn">View Property</a></article>
  <article class="card"><div class="card-img img-c" role="img" aria-label="Photo of white suburban townhouses"><span class="ribbon dark">FEATURED</span></div><div class="card-city">Gurgaon</div><div class="card-name">Veltra Cosmoline</div><p class="card-desc">The images for this demonstration property were kindly loaned to us by the Corvane Estate Group and a...</p><a class="card-btn">View Property</a></article>
  <article class="card"><div class="card-img img-d" role="img" aria-label="Photo of a tall hotel tower lit at evening"><span class="ribbon dark">FEATURED</span></div><div class="card-city">Gurgaon</div><div class="card-name">Veltra Cosmoline</div><p class="card-desc">The images for this demonstration property were kindly loaned to us by the Corvane Estate Group and a...</p><a class="card-btn">View Property</a></article>
</div>

<footer class="site-footer">
  <h3 class="foot-h" style="left:61px">Listing Alert</h3>
  <svg class="abs" style="left:60px;top:36px" width="36" height="34" viewBox="0 0 36 34"><path d="M2 14L18 2l16 12v18H2z" fill="#d9d9d9"/><path d="M8 6h20v14H8z" fill="#e8922a"/><path d="M2 14l16 11 16-11v18H2z" fill="#bdbdbd"/><circle cx="18" cy="13" r="4" fill="none" stroke="#fff" stroke-width="1.5"/></svg>
  <p class="foot-text" style="left:103px;top:42px;width:110px;font-size:7px;line-height:11px">Suscribe&nbsp; for Fortnightly Email update on New Listings @ Lotstallmart</p>
  <div class="foot-input" style="left:61px;top:108px;width:145px;height:18px">Email Your Email Address:</div>
  <div class="foot-btn" style="left:144px;top:114px;width:63px;height:21px;font-size:10px;line-height:21px">Subscribe</div>

  <div class="foot-vr" style="left:221px"></div>
  <h3 class="foot-h" style="left:239px">Editor's Choice</h3>
  <p class="foot-text" style="left:239px;top:43px;width:207px">A "Select" Listing of Retail Properties Handpicked by our Editors based on their own positive evaluation on param-eters &amp; attributes such as Design Concept, Location, Developer, Success Potential. So Read On to Check Out for yourself ...........</p>

  <div class="foot-vr" style="left:463px"></div>
  <h3 class="foot-h" style="left:499px">Mart Wizards</h3>
  <div class="foot-input" style="left:499px;top:43px;width:158px;height:18px">Email Your Email Address:</div>
  <div class="foot-input" style="left:499px;top:72px;width:158px;height:34px">Add Description of Requirement</div>
  <div class="foot-btn" style="left:595px;top:114px;width:63px;height:22px;font-size:12px;line-height:22px">Send</div>
</footer>

<div class="bottom-band">
  <p class="copyright">Copyright © 2013 Lotstallmart. All rights reserved.<br>website by Nuvora Technologies.</p>
  <div class="band-brand"><span class="brand-dot"></span><span class="brand-name">lotstallmart</span></div>
  <div class="band-tag">INDIA'S LEADING PORTAL FOR RETAIL SPACE</div>
</div>

</body>
</html>
```